Dog Snacks brand needs a new packaging design

Dear Designers,

We are looking for a packaging expert to design our new line of Dog Snacks which contain a relaxing hemp extract (CBD).

Our company is already selling various relaxing cat & dog products , and we would like this new design to reflect the same "style & feeling" as our current products (see attached instructions).

Technical aspects:
- The packaging is a Stand Up Pouch (12x18.5x7cm - see attached instructions).
- Please follow technical guidelines from printer (see attached instructions).
- The packaging will contain 120g of high-quality, semi-moist dog snacks.
- We will be designing 3 differents variations for 3 different flavours: Chicken, Beef & Liver.
- The packaging will be printed with a matt finish.

Design aspects:
- The design should be compatible with our brand identity (i.e. fluffly, pure, relaxing, positive, clean & natural).
- Soft/rounded shapes are preferred.
- Please use our brand's colors (#3BA384, White & Black).
- Please use our company logo (see attached instructions).
- The design also needs to convey a strong sense of professionalism as we are an animal "healthcare" brand.
- If you want to include a dog picture, we would prefer you to use a picture of our official brand ambassador (see attached instructions).
- We have attached a number of packaging examples which we like a lot. (see attached instructions). Please only use those as general inspiration.
- Only original work (no plagiarism will be accepted).

Please don't hesitate to send us a message if you have any questions about the brand, the product or the design requirements.

We look forward to seeing your designs & working on this together !

Thanks & regards,
Tobias

Target Market(s)

Dog owners

Industry/Entity Type

Pet Care

Font styles to use
Sans Serif

Requirements
Must have
• Please see project description.
Nice to have
Should not have

```html
<!DOCTYPE html>
<html lang="en">
<head>
<meta charset="utf-8">
<title>Calmbites CBD Treats – Simply Chicken</title>
<link rel="stylesheet" href="https://fonts.googleapis.com/css2?family=Raleway:wght@600;700&family=Montserrat:wght@500;600;700&family=Playfair+Display:wght@700&family=Yellowtail&display=swap">
<style>
  :root {
    --stage: #5ec8cc;
    --top-teal: #66c9b8;
    --brand-green: #3ba384;
    --mid-teal: #8fd4c5;
    --soft-white: #e8f5f2;
    --deep-teal: #1c6a66;
    --white: #ffffff;
    --photo-dog: #ece6e2;
    --photo-dog-small: #d9cfcb;
    --photo-treats: #b98f62;
  }
  * { margin: 0; padding: 0; box-sizing: border-box; }
  html, body { width: 1200px; height: 814px; overflow: hidden; }
  body { background: var(--stage); position: relative; }
  .pouch-front { position: absolute; left: 320px; top: 20px; width: 560px; height: 774px; }
  .pouch-front svg { display: block; width: 560px; height: 774px; }
  .brand-name { font-family: "Raleway", sans-serif; font-weight: 700; font-size: 30px; fill: var(--white); letter-spacing: 1px; }
  .spec { font-family: "Montserrat", sans-serif; font-weight: 600; font-size: 12px; fill: var(--white); letter-spacing: .5px; }
  .benefits { font-family: "Montserrat", sans-serif; font-weight: 600; font-size: 15px; fill: var(--deep-teal); letter-spacing: 2px; }
  .product-name { font-family: "Montserrat", sans-serif; font-weight: 700; font-size: 58px; fill: var(--deep-teal); letter-spacing: 0; }
  .cbd-pill-label { font-family: "Raleway", sans-serif; font-weight: 600; font-size: 20px; fill: var(--white); }
  .treats-word { font-family: "Yellowtail", cursive; font-size: 66px; fill: var(--brand-green); }
  .flavour-light { font-family: "Playfair Display", serif; font-weight: 700; font-size: 32px; fill: var(--white); }
  .flavour-dark { font-family: "Playfair Display", serif; font-weight: 700; font-size: 40px; fill: var(--deep-teal); }
  .badge-big { font-family: "Raleway", sans-serif; font-weight: 600; font-size: 28px; fill: var(--white); }
  .badge-mid { font-family: "Raleway", sans-serif; font-weight: 600; font-size: 18px; fill: var(--white); }
  .badge-small { font-family: "Raleway", sans-serif; font-weight: 600; font-size: 9px; fill: var(--white); }
  .endorsement { font-family: "Raleway", sans-serif; font-weight: 600; font-size: 16px; fill: var(--deep-teal); }
</style>
</head>
<body>
<main class="pouch-front">
  <svg viewBox="0 0 560 774" xmlns="http://www.w3.org/2000/svg">
    <rect class="panel-base" x="0" y="0" width="560" height="774" fill="var(--mid-teal)"/>
    <rect class="top-band" x="0" y="0" width="560" height="110" fill="var(--top-teal)"/>
    <path class="window" d="M0 124 H560 V200 C540 280 470 340 280 338 C100 338 25 290 0 240 Z" fill="var(--soft-white)"/>
    <path class="spec-strip" d="M0 101 H560 V124 H320 C300 124 288 140 280 156 C272 140 260 124 240 124 H0 Z" fill="var(--brand-green)"/>

    <circle class="brand-dot" cx="218" cy="58" r="5" fill="var(--white)"/>
    <text class="brand-name" x="284" y="69" text-anchor="middle">Verdalis</text>

    <text class="spec" x="29" y="117">NET WEIGHT 120G</text>
    <text class="spec" x="540" y="117" text-anchor="end">CBD 250mg</text>

    <text class="benefits" x="280" y="186" text-anchor="middle">SUPPORT · CALM · EASE</text>
    <text class="product-name" x="280" y="256" text-anchor="middle">Calmbites</text>

    <rect class="cbd-pill" x="390" y="272" width="62" height="30" rx="15" fill="var(--deep-teal)"/>
    <text class="cbd-pill-label" x="421" y="294" text-anchor="middle">CBD</text>
    <text class="treats-word" x="346" y="350" transform="rotate(-10 430 330)">Treats</text>

    <text class="flavour-light" x="300" y="392">Simply</text>
    <text class="flavour-dark" x="320" y="436">Chicken</text>

    <path class="treats-frame" d="M230 697 C250 640 240 560 300 500 C350 460 430 470 480 520 C520 570 500 660 470 697 Z" fill="var(--brand-green)" opacity=".55"/>
    <g role="img" aria-label="Photo of bone-shaped chicken treats">
      <ellipse cx="372" cy="598" rx="118" ry="112" fill="var(--photo-treats)"/>
    </g>

    <g role="img" aria-label="Photo of a white Shar Pei puppy, the brand ambassador">
      <path d="M20 697 V380 C40 330 90 312 150 312 C220 312 262 350 275 420 C285 480 300 560 260 697 Z" fill="var(--photo-dog)"/>
    </g>

    <g role="img" aria-label="Photo of a sleepy Shar Pei puppy resting its paws on the edge">
      <path d="M385 700 C380 650 400 610 440 600 C490 590 530 610 545 650 L560 690 V720 H400 Z" fill="var(--photo-dog-small)"/>
    </g>

    <circle class="badge-ring" cx="496" cy="492" r="46" fill="none" stroke="var(--deep-teal)" stroke-width="3" stroke-dasharray="1 6" stroke-linecap="round"/>
    <circle class="badge" cx="496" cy="492" r="40" fill="var(--deep-teal)"/>
    <text class="badge-big" x="496" y="489" text-anchor="middle">NO</text>
    <text class="badge-mid" x="496" y="507" text-anchor="middle">THC</text>
    <text class="badge-small" x="496" y="519" text-anchor="middle">0% THC</text>

    <path class="bottom-band" d="M0 699 H250 C265 699 275 690 280 676 C285 690 295 699 310 699 H560 V722 H0 Z" fill="var(--brand-green)"/>
    <rect class="bottom-area" x="0" y="722" width="560" height="52" fill="var(--top-teal)"/>
    <text class="endorsement" x="280" y="752" text-anchor="middle">“Recommended By Veterinarians”</text>
  </svg>
</main>
</body>
</html>
```